velorimo.gr wordpress makeover

We need a makeover of our wordpress website velorimo.gr We are a company that provides astrology services via phone either by billable phone number or by prepaid packages.This is what we sell. Moreover, we share everyday astrology related articles to our blog. It will be a multy page website. Our goal is always to sell our phone prepaid packages or to make the visitor of the website call our billable numbers. Our website should have:
-a home page introducing its content (astrologers, call packages, blog section with categories).
-astrologers page (you can see the existing one to understand)
-Phone packages page (eshop page where you can buy prepaid phone packages. woo commerce maybe)
- Blog page divined by categories.
The website should have places for display banners eg. a sidebar.
I will provide some screen shots of websites we like. You can always visit our existing website www.velorimo.gr to see it for yourself.

Target Market(s)

people seeking for future telling - astrologer services via phone. People who like to be informed about everyday astrology predictions

Industry/Entity Type

Astrology - tarot services via phone

Coding

Coded - Design and coding required

Number of Pages Required

5+ page

Font styles to use
Decorative
Script

Colors
6B429C
8869AF
B7A5CE
E3DAEB
F3F0F8

Requirements
Must have
• -Home page -Astrologers page -Phone packages page (eshop) -Blog page with categories - Made following the guidelines of quenbly so as to be efficient in quenbly ads marketing. Mobile friendly.
Nice to have
• Nice call to action buttons to call or buy packages. Sidebar with banner ads of maybe our offers.

```html
<!DOCTYPE html>
<html lang="el">
<head>
<meta charset="utf-8">
<title>velorimo.gr – Αστρολογία</title>
<link rel="stylesheet" href="https://fonts.googleapis.com/css2?family=Lato:ital,wght@0,400;0,700;0,900;1,900&family=Comfortaa:wght@500;700&family=Lobster&display=swap">
<style>
:root{
  --bg-deep:#0e0420;
  --bg-mid:#1d0a38;
  --panel:rgba(38,14,68,.72);
  --panel-line:rgba(150,100,210,.38);
  --violet:#7a22f0;
  --violet-2:#a13cf2;
  --lilac:#b7a5ce;
  --lilac-soft:#e3daeb;
  --white:#f3f0f8;
  --yellow:#ffd60a;
  --text-dim:#cfc4e0;
}
*{box-sizing:border-box;margin:0;padding:0}
html,body{width:1200px;height:4673px;overflow:hidden}
body{
  font-family:"Lato",sans-serif;color:var(--white);
  background:
    radial-gradient(ellipse 700px 500px at 80% 8%,rgba(120,40,170,.35),transparent 70%),
    radial-gradient(ellipse 600px 600px at 15% 20%,rgba(90,30,150,.30),transparent 70%),
    radial-gradient(ellipse 800px 600px at 50% 50%,rgba(60,15,100,.35),transparent 70%),
    radial-gradient(ellipse 700px 500px at 70% 72%,rgba(110,40,160,.30),transparent 70%),
    radial-gradient(ellipse 900px 500px at 40% 92%,rgba(80,20,130,.30),transparent 70%),
    linear-gradient(180deg,var(--bg-mid) 0%,var(--bg-deep) 30%,var(--bg-mid) 55%,var(--bg-deep) 80%,#170833 100%);
}
.page{position:relative;width:1200px;height:4673px}
.abs{position:absolute}
.center{left:0;width:1200px;text-align:center}

/* header */
.logo{font-family:"Lato",sans-serif;font-weight:400;font-size:50px;letter-spacing:-.5px;color:var(--white);display:flex;align-items:center;gap:6px}
.logo .dot{width:28px;height:28px;border-radius:50%;background:#6b429c;display:inline-block}
.nav{top:52px;left:397px;display:flex;gap:42px;font-size:16px}
.search{left:928px;top:45px;width:36px;height:36px;border-radius:50%;border:2px solid var(--lilac);display:flex;align-items:center;justify-content:center}
.phone-pill{left:985px;top:40px;width:152px;height:47px;border-radius:24px;background:var(--violet);border:2px solid #fff;display:flex;align-items:center;justify-content:center;gap:6px;font-weight:900;font-style:italic;font-size:34px;color:#fff}

.h-caps{font-family:"Lato",sans-serif;font-weight:400;font-size:40px;letter-spacing:.5px}
.h-greek{font-family:"Comfortaa",sans-serif;font-weight:700;font-size:46px;letter-spacing:1px}
.lead{font-size:21px;line-height:28px;color:var(--white)}

/* cards */
.card{position:absolute;background:var(--panel);border:1px solid var(--panel-line);display:flex;align-items:center;padding:0 14px;gap:16px}
.thumb{flex:none;border-radius:2px}
.card h3{font-weight:400;font-size:20px;margin-bottom:8px}
.card p{font-size:12px;line-height:14px;color:var(--text-dim)}

.btn{position:absolute;height:48px;border-radius:24px;background:var(--violet);border:2px solid #c9a6ff;color:#fff;font-size:14px;display:flex;align-items:center;justify-content:center;letter-spacing:.4px;text-transform:uppercase}
.btn.ghost{background:rgba(60,20,110,.6)}

/* tabs */
.tabs{top:856px;left:101px;display:flex;gap:0;font-size:22px;color:var(--lilac)}
.tabs span{margin-right:54px}
.tabs .on{color:#9d5cff;font-weight:700}
.tab-line{top:910px;left:96px;width:999px;height:3px;background:#6e2cd8}
.sign{position:absolute;top:950px;width:160px;height:160px;border-radius:50%;background:radial-gradient(circle at 50% 45%,#5a22b5,#3a1380 70%);border:1px solid rgba(170,120,255,.4)}

/* astrologers */
.astro{position:absolute;top:1369px;width:234px;height:381px;border-radius:117px;border:2px solid var(--lilac-soft);overflow:hidden;background:rgba(26,8,50,.85);text-align:center}
.astro .photo{height:150px;background:linear-gradient(180deg,#3a1f8a,#6b2fd0)}
.astro .photo.warm{background:linear-gradient(180deg,#e08a1a,#ffb347)}
.astro h4{font-size:17px;font-weight:400;margin-top:30px}
.astro .role{font-size:12px;color:var(--yellow);margin-top:4px}
.astro p{font-size:11px;line-height:13px;margin:14px 22px 0}
.astro .call{font-weight:900;font-style:italic;font-size:30px;color:var(--yellow);margin-top:18px;display:flex;align-items:center;justify-content:center;gap:4px}

/* tarot */
.tarot-cta{left:776px;top:2205px;width:321px;height:257px;background:linear-gradient(160deg,#6c1ff0,#9a2ef0);text-align:center;padding-top:28px}
.tarot-cta h3{font-weight:400;font-size:29px;line-height:34px}
.tarot-cta p{font-size:11px;line-height:14px;margin:16px 40px 0}
.btn-yellow{display:inline-flex;align-items:center;justify-content:center;height:40px;padding:0 28px;border-radius:20px;background:var(--yellow);color:#1a0a2e;font-weight:700;font-size:14px;margin-top:16px}

/* packages */
.pkg{position:absolute;top:2768px;width:319px;height:236px;background:rgba(34,12,64,.9);text-align:center;padding-top:28px}
.pkg.hot{background:linear-gradient(160deg,#6a1ff0,#9a2ef0)}
.pkg .price{font-family:"Lobster",cursive;font-size:50px;color:var(--yellow);line-height:56px}
.pkg .mins{font-size:17px;color:var(--yellow);margin-top:2px}
.pkg p{font-size:12px;line-height:14px;margin:28px 40px 0}
.pkg.hot .mins{color:var(--lilac-soft)}

/* blog */
.post{position:absolute;left:98px;width:664px;height:200px;border:1px solid var(--panel-line);background:rgba(24,8,46,.8)}
.post .img{position:absolute;left:18px;top:18px;width:181px;height:165px}
.post .body{position:absolute;left:218px;top:26px;width:420px}
.cats{display:flex;gap:30px;font-size:10px;color:#a37cff;text-decoration:underline}
.post h3{font-weight:400;font-size:20px;margin-top:14px}
.post p{font-size:11px;line-height:14px;color:var(--text-dim);margin-top:8px}
.date{font-size:11px;color:var(--yellow);margin-top:10px;display:flex;align-items:center;gap:5px}

.side-chart{left:789px;top:3320px;width:310px;height:279px;background:linear-gradient(160deg,#6a1ff0,#9a2ef0);text-align:center;padding-top:48px}
.side-chart h3{font-family:"Lobster",cursive;font-weight:400;font-size:27px;line-height:33px;color:var(--yellow)}
.side-chart p{font-size:11px;line-height:13px;margin:12px 40px 0}
.side-promo{left:787px;top:3620px;width:314px;height:345px;border:3px solid #ccd6ff;background:linear-gradient(180deg,#0a1440,#111c55);text-align:center;padding-top:20px;color:#5fc4ff}
.side-promo h3{font-family:"Comfortaa",sans-serif;font-weight:700;font-size:23px;line-height:25px}
.promo-art{margin:16px auto 0;width:220px;height:170px;display:flex;gap:10px}
.promo-art .clock{width:110px;height:110px;border-radius:50%;border:6px solid #2ea6ff;margin-top:30px}
.promo-art .deal{flex:1;background:linear-gradient(180deg,#3a1a8a,#1c0f55);display:flex;flex-direction:column;align-items:center;justify-content:center;color:#fff;font-weight:900;line-height:1}
.side-promo .foot{font-family:"Comfortaa",sans-serif;font-weight:700;font-size:23px;line-height:25px;margin-top:12px}

/* newsletter + footer */
.rule{left:0;width:1200px;height:1px;background:rgba(180,150,220,.35)}
.script-title{font-family:"Lobster",cursive;font-size:30px}
.field{position:absolute;top:4233px;height:47px;border-radius:24px;border:1px solid var(--lilac-soft);background:rgba(20,6,40,.6);font-size:14px;padding-left:18px;display:flex;align-items:center}
.zodiac-links{top:4464px;left:104px;display:flex;gap:0;font-size:12px}
.zodiac-links span{margin-right:36px}
.foot-links{top:4546px;left:193px;display:flex;font-size:12px}
.foot-links span{margin-right:42px}
.social{position:absolute;left:1119px;width:40px;height:40px;border-radius:50%}
</style>
</head>
<body>
<div class="page">

  <!-- header -->
  <div class="abs logo" style="left:52px;top:30px">velorimo<span class="dot"></span></div>
  <nav class="abs nav"><span>Blog</span><span>Μέντιουμ Αστρολόγοι</span><span>Αγορά Χρόνου Ομιλίας</span></nav>
  <div class="abs search"><svg width="14" height="14" viewBox="0 0 14 14"><circle cx="6" cy="6" r="4.2" fill="none" stroke="#fff" stroke-width="2"/><path d="M9 9l4 4" stroke="#fff" stroke-width="2"/></svg></div>
  <div class="abs phone-pill"><svg width="26" height="26" viewBox="0 0 24 24"><path d="M6.6 10.8a15 15 0 006.6 6.6l2.2-2.2a1 1 0 011-.25 11.4 11.4 0 003.6.57 1 1 0 011 1V20a1 1 0 01-1 1A17 17 0 013 4a1 1 0 011-1h3.5a1 1 0 011 1c0 1.25.2 2.45.57 3.6a1 1 0 01-.25 1z" fill="#fff"/></svg>14870</div>

  <!-- welcome -->
  <h1 class="abs center h-caps" style="top:218px">WELCOME TO VELORIMO.GR</h1>
  <p class="abs center lead" style="top:296px">Lorem ipsum dolor sit amet, consectetur adipiscing elit<br>ed do eiusmod tempor incididunt ut labore et</p>

  <div class="card" style="left:102px;top:404px;width:320px;height:124px"><div class="thumb" role="img" aria-label="Astrology article image" style="width:100px;height:90px;background:linear-gradient(135deg,#1d5fb0,#e0b040)"></div><div><h3>Latest Articles</h3><p>Lorem ipsum dolor sit amet,<br>consectetur adipiscinlore</p></div></div>
  <div class="card" style="left:439px;top:404px;width:321px;height:124px"><div class="thumb" role="img" aria-label="Astrology article image" style="width:100px;height:90px;background:linear-gradient(135deg,#3a2a20,#c58a50)"></div><div><h3>Latest Articles</h3><p>Lorem ipsum dolor sit amet,<br>consectetur adipiscinlore</p></div></div>
  <div class="card" style="left:776px;top:404px;width:321px;height:124px"><div class="thumb" role="img" aria-label="Astrology article image" style="width:100px;height:90px;background:linear-gradient(135deg,#0a3a8a,#4ab0ff)"></div><div><h3>Latest Articles</h3><p>Lorem ipsum dolor sit amet,<br>consectetur adipiscinlore</p></div></div>
  <div class="card" style="left:102px;top:542px;width:320px;height:122px"><div class="thumb" role="img" aria-label="Astrology article image" style="width:100px;height:90px;background:linear-gradient(135deg,#1a3aa0,#7aa0ff)"></div><div><h3>Latest Articles</h3><p>Lorem ipsum dolor sit amet,<br>consectetur adipiscinlore</p></div></div>
  <div class="card" style="left:439px;top:542px;width:321px;height:122px"><div class="thumb" role="img" aria-label="Astrology article image" style="width:100px;height:90px;background:linear-gradient(135deg,#e0a020,#6ab0d0)"></div><div><h3>Latest Articles</h3><p>Lorem ipsum dolor sit amet,<br>consectetur adipiscinlore</p></div></div>
  <div class="card" style="left:776px;top:542px;width:321px;height:122px"><div class="thumb" role="img" aria-label="Astrology article image" style="width:100px;height:90px;background:linear-gradient(135deg,#5a1a10,#d07030)"></div><div><h3>Latest Articles</h3><p>Lorem ipsum dolor sit amet,<br>consectetur adipiscinlore</p></div></div>

  <a class="btn" style="left:520px;top:714px;width:160px">More Articles</a>

  <!-- zodiac tabs -->
  <div class="abs tabs"><span class="on">Astrology</span><span>Horoscope</span><span>Panchang</span><span>Zodiac</span></div>
  <div class="abs tab-line"></div>
  <div class="sign" style="left:96px" role="img" aria-label="Aries zodiac illustration"></div>
  <div class="sign" style="left:266px" role="img" aria-label="Taurus zodiac illustration"></div>
  <div class="sign" style="left:435px" role="img" aria-label="Gemini zodiac illustration"></div>
  <div class="sign" style="left:604px" role="img" aria-label="Cancer zodiac illustration"></div>
  <div class="sign" style="left:774px" role="img" aria-label="Leo zodiac illustration"></div>
  <div class="sign" style="left:943px" role="img" aria-label="Virgo zodiac illustration"></div>
  <svg class="abs" style="left:1130px;top:1000px" width="18" height="46" viewBox="0 0 18 46"><path d="M12 3l-7 7 7 7M6 29l7 7-7 7" fill="none" stroke="#fff" stroke-width="2.5"/></svg>

  <!-- astrologers -->
  <h2 class="abs center h-greek" style="top:1250px">Μέντιουμ Αστρολόγοι</h2>
  <div class="astro" style="left:98px"><div class="photo" role="img" aria-label="Astrologer portrait"></div><h4>Αλέξανδρος</h4><div class="role">(Αστρολόγος, Μέντιουμ)</div><p>Αν θέλεις μια αληθινή πρόβλεψη κάλεσε με ΤΩΡΑ. Η αστρολογία θα με κατευθύνει και θα δώσω λύσεις στα πρόβλημα και</p><div class="call"><svg width="22" height="22" viewBox="0 0 24 24"><path d="M6.6 10.8a15 15 0 006.6 6.6l2.2-2.2a1 1 0 011-.25 11.4 11.4 0 003.6.57 1 1 0 011 1V20a1 1 0 01-1 1A17 17 0 013 4a1 1 0 011-1h3.5a1 1 0 011 1c0 1.25.2 2.45.57 3.6a1 1 0 01-.25 1z" fill="#ffd60a"/></svg>14870</div></div>
  <div class="astro" style="left:355px"><div class="photo" role="img" aria-label="Astrologer portrait"></div><h4>Αλέξανδρος</h4><div class="role">(Αστρολόγος, Μέντιουμ)</div><p>Αν θέλεις μια αληθινή πρόβλεψη κάλεσε με ΤΩΡΑ. Η αστρολογία θα με κατευθύνει και θα δώσω λύσεις στα πρόβλημα και</p><div class="call"><svg width="22" height="22" viewBox="0 0 24 24"><path d="M6.6 10.8a15 15 0 006.6 6.6l2.2-2.2a1 1 0 011-.25 11.4 11.4 0 003.6.57 1 1 0 011 1V20a1 1 0 01-1 1A17 17 0 013 4a1 1 0 011-1h3.5a1 1 0 011 1c0 1.25.2 2.45.57 3.6a1 1 0 01-.25 1z" fill="#ffd60a"/></svg>14870</div></div>
  <div class="astro" style="left:611px"><div class="photo warm" role="img" aria-label="Astrologer portrait"></div><h4>Αλέξανδρος</h4><div class="role">(Αστρολόγος, Μέντιουμ)</div><p>Αν θέλεις μια αληθινή πρόβλεψη κάλεσε με ΤΩΡΑ. Η αστρολογία θα με κατευθύνει και θα δώσω λύσεις στα πρόβλημα και</p><div class="call"><svg width="22" height="22" viewBox="0 0 24 24"><path d="M6.6 10.8a15 15 0 006.6 6.6l2.2-2.2a1 1 0 011-.25 11.4 11.4 0 003.6.57 1 1 0 011 1V20a1 1 0 01-1 1A17 17 0 013 4a1 1 0 011-1h3.5a1 1 0 011 1c0 1.25.2 2.45.57 3.6a1 1 0 01-.25 1z" fill="#ffd60a"/></svg>14870</div></div>
  <div class="astro" style="left:868px"><div class="photo" role="img" aria-label="Astrologer portrait"></div><h4>Αλέξανδρος</h4><div class="role">(Αστρολόγος, Μέντιουμ)</div><p>Αν θέλεις μια αληθινή πρόβλεψη κάλεσε με ΤΩΡΑ. Η αστρολογία θα με κατευθύνει και θα δώσω λύσεις στα πρόβλημα και</p><div class="call"><svg width="22" height="22" viewBox="0 0 24 24"><path d="M6.6 10.8a15 15 0 006.6 6.6l2.2-2.2a1 1 0 011-.25 11.4 11.4 0 003.6.57 1 1 0 011 1V20a1 1 0 01-1 1A17 17 0 013 4a1 1 0 011-1h3.5a1 1 0 011 1c0 1.25.2 2.45.57 3.6a1 1 0 01-.25 1z" fill="#ffd60a"/></svg>14870</div></div>
  <a class="btn" style="left:520px;top:1789px;width:160px">View More</a>

  <!-- tarot -->
  <h2 class="abs center h-caps" style="top:2020px">TAROT FORECASTS</h2>
  <p class="abs center lead" style="top:2096px">Lorem ipsum dolor sit amet, consectetur adipiscing elit<br>ed do eiusmod tempor incididunt ut labore et</p>
  <div class="card" style="left:102px;top:2205px;width:320px;height:119px"><div class="thumb" role="img" aria-label="Tarot cards image" style="width:100px;height:90px;background:linear-gradient(135deg,#8a3a10,#e0b050)"></div><div><h3>Tarot for today</h3><p>Tuesday 22/11<br>November 22, 2022</p></div></div>
  <div class="card" style="left:439px;top:2205px;width:321px;height:119px"><div class="thumb" role="img" aria-label="Tarot cards image" style="width:100px;height:90px;background:linear-gradient(135deg,#2a5a70,#c0b080)"></div><div><h3>Tarot for today</h3><p>Tuesday 22/11<br>November 22, 2022</p></div></div>
  <div class="card" style="left:102px;top:2342px;width:320px;height:120px"><div class="thumb" role="img" aria-label="Tarot wheel image" style="width:100px;height:90px;background:linear-gradient(135deg,#0a4a5a,#60d0e0)"></div><div><h3>Tarot for week</h3><p>Tuesday 22/11<br>November 22, 2022</p></div></div>
  <div class="card" style="left:439px;top:2342px;width:321px;height:120px"><div class="thumb" role="img" aria-label="Tarot cards image" style="width:100px;height:90px;background:linear-gradient(135deg,#8a2010,#2a6ab0)"></div><div><h3>Tarot for today</h3><p>Tuesday 22/11<br>November 22, 2022</p></div></div>
  <div class="abs tarot-cta"><h3>Get a Live<br>Tarot Reading</h3><p>Lorem ipsum dolor sit amet,cons ctetur adipiscinloreincidid unt ut labore et dolore magna aliquais ipsum</p><span class="btn-yellow">START NOW</span></div>

  <!-- packages -->
  <h2 class="abs center h-greek" style="top:2660px">Αγορά Χρόνου Ομιλίας</h2>
  <div class="pkg" style="left:98px"><div class="price">30€</div><div class="mins">20 mins of talking time.</div><p>Lorem ipsum dolor sit amet, consectetur adipiscing elit, sed do eiusmod tempor incididunt ut labore et dolo aliqua.</p></div>
  <div class="pkg hot" style="left:440px"><div class="price">40€</div><div class="mins">30 mins of talking time.</div><p>Lorem ipsum dolor sit amet, consectetur adipiscing elit, sed do eiusmod tempor incididunt ut labore et dolo aliqua.</p></div>
  <div class="pkg" style="left:783px"><div class="price">50€</div><div class="mins">40 mins of talking time.</div><p>Lorem ipsum dolor sit amet, consectetur adipiscing elit, sed do eiusmod tempor incididunt ut labore et dolo aliqua.</p></div>
  <a class="btn ghost" style="left:520px;top:3042px;width:160px">Explore More</a>

  <!-- blog -->
  <h2 class="abs h-caps" style="left:96px;top:3222px">OUR BLOG POSTS</h2>
  <div class="post" style="top:3320px"><div class="img" role="img" aria-label="Zodiac wheel article image" style="background:linear-gradient(135deg,#0a2a6a,#4aa0e0)"></div><div class="body"><div class="cats"><span>DAILY</span><span>PREDICTIONS</span><span>TAROT</span><span>TAROT TODAY</span></div><h3>The zodiac signs for today, Tuesday 15/3</h3><p>Lorem ipsum dolor sit amet, consectetur adipiscing elit, sed do eiusmod tempor incididunt ut labore et dolore magna aliqua. Quis ipsum suspendisse ultrices gravida. Risus commodo</p><div class="date"><svg width="10" height="10" viewBox="0 0 10 10"><rect x="1" y="2" width="8" height="7" fill="none" stroke="#ffd60a"/><path d="M1 4h8" stroke="#ffd60a"/></svg>MARCH 14, 2022</div></div></div>
  <div class="post" style="top:3541px"><div class="img" role="img" aria-label="Open book with zodiac article image" style="background:linear-gradient(135deg,#2a3a20,#d0b070)"></div><div class="body"><div class="cats"><span>DAILY</span><span>PREDICTIONS</span><span>TAROT</span><span>TAROT TODAY</span></div><h3>The zodiac signs for today, Tuesday 15/3</h3><p>Lorem ipsum dolor sit amet, consectetur adipiscing elit, sed do eiusmod tempor incididunt ut labore et dolore magna aliqua. Quis ipsum suspendisse ultrices gravida. Risus commodo</p><div class="date"><svg width="10" height="10" viewBox="0 0 10 10"><rect x="1" y="2" width="8" height="7" fill="none" stroke="#ffd60a"/><path d="M1 4h8" stroke="#ffd60a"/></svg>MARCH 14, 2022</div></div></div>
  <div class="post" style="top:3758px"><div class="img" role="img" aria-label="Zodiac circle night sky article image" style="background:linear-gradient(135deg,#101a40,#5a7ab0)"></div><div class="body"><div class="cats"><span>DAILY</span><span>PREDICTIONS</span><span>TAROT</span><span>TAROT TODAY</span></div><h3>The zodiac signs for today, Tuesday 15/3</h3><p>Lorem ipsum dolor sit amet, consectetur adipiscing elit, sed do eiusmod tempor incididunt ut labore et dolore magna aliqua. Quis ipsum suspendisse ultrices gravida. Risus commodo</p><div class="date"><svg width="10" height="10" viewBox="0 0 10 10"><rect x="1" y="2" width="8" height="7" fill="none" stroke="#ffd60a"/><path d="M1 4h8" stroke="#ffd60a"/></svg>MARCH 14, 2022</div></div></div>

  <div class="abs side-chart"><h3>Free Birth Chart<br>Natal Chart Report</h3><p>Lorem ipsum dolor sit amet, consectetur adipiscing elit, sed do eiusmod tempor incididunt ut labore et dolore m</p><span class="btn-yellow" style="width:140px;padding:0;margin-top:20px">CALCULATE</span></div>
  <div class="abs side-promo"><h3>Μίλησε Χωρίς<br>χρεώσεις στο<br>τηλέφωνό σου..!</h3>
    <div class="promo-art"><div class="clock" role="img" aria-label="Stopwatch illustration"></div><div class="deal"><span style="font-size:26px">30'</span><span style="font-size:16px">ΛΕΠΤΑ</span><span style="font-size:8px;margin:4px 0 14px">ΧΡΟΝΟΥ ΟΜΙΛΙΑΣ</span><span style="font-size:10px">ΜΟΝΟ</span><span style="font-size:26px">30€</span></div></div>
    <div class="foot">Μάθε πως<br>γίνεται..!!!</div></div>
  <a class="btn" style="left:102px;top:4001px;width:157px">Explore More</a>

  <!-- newsletter -->
  <div class="abs rule" style="top:4126px"></div>
  <h2 class="abs center script-title" style="top:4162px">Join Our Daily Overview Newsletter!</h2>
  <div class="field" style="left:270px;width:240px">Name:</div>
  <div class="field" style="left:520px;width:240px">Email:</div>
  <a class="btn" style="left:772px;top:4233px;width:156px;height:47px;font-size:15px">Join Now</a>
  <div class="abs rule" style="top:4342px"></div>

  <!-- footer -->
  <div class="abs logo" style="left:465px;top:4366px">velorimo<span class="dot"></span></div>
  <div class="abs zodiac-links"><span>ARIES</span><span>TAURUS</span><span>GEMINI</span><span>CANCER</span><span>LEO</span><span>VIRGO</span><span>LIBRA</span><span>SCORPIO</span><span>SAGITTARIUS</span><span>CAPRICORN</span><span>AQUARIUS</span><span>PISCES</span></div>
  <div class="abs rule" style="top:4514px"></div>
  <div class="abs foot-links"><span>ABOUT US</span><span>CONTACT US</span><span>ADVERTISING</span><span>SYNDICATION</span><span>PRIVACY</span><span>TERMS</span><span>DO NOT SELL MY INFO</span></div>
  <div class="abs center" style="top:4600px;font-size:12px">© COPYRIGHT • 2022 • VELORIMO.GR</div>
  <div class="social" style="top:4505px;background:#1da1f2" role="img" aria-label="Social link"></div>
  <div class="social" style="top:4561px;background:#2a5bd7" role="img" aria-label="Social link"></div>
  <div class="social" style="top:4618px;background:#d6249f" role="img" aria-label="Social link"></div>
</div>
</body>
</html>
```